Local Flower Farm Needs Business Card Design

I need business cards designed for a flower farm based in Eudora, Kansas.
Business Info:
We are a local cut flower farm located in Eudora, Kansas, founded by Corinne Haldwick. What started as a passion for agriculture and search for more joy in daily life has blossomed into a small business dedicated to providing the community with beautiful, fresh, and sustainable flowers. We specialize in local, seasonal blooms, ensuring that every petal reflects the care and dedication we pour into our craft. Our mission is to deliver the highest quality flowers directly to our customers through local farmers markets and to florists who share our commitment to sustainability. Join us in celebrating the beauty of nature, one bloom at a time!
Contact Details:
Corinne Haldwick
Owner
Phone 913-555-0147
Facebook: Rosalind Thorpe Gardens
Instagram: @RosalindThorpeGardens
Website: RosalindThorpeGardens.example
Target Market(s)
Wholesale to Florists and Direct to Consumer via Farmers Market
Industry/Entity Type
Florist, Farm
Contact Information for Business Card
Name, Contact Info, Logo
Look and feel
Each slider illustrates characteristics of the customer's brand and the style your logo design should communicate.

```html
<!DOCTYPE html>
<html lang="en">
<head>
<meta charset="utf-8">
<title>Rosalind Thorpe Gardens – Business Card</title>
<link href="https://fonts.googleapis.com/css2?family=EB+Garamond:wght@400;700&display=swap" rel="stylesheet">
<style>
  :root {
    --stage: #242628;
    --teal-deep: #0a2228;
    --teal: #0f3940;
    --teal-soft: #1d4c53;
    --paper: #ffffff;
    --ink: #0d2f35;
    --ink-muted: #4a4f50;
  }
  * { box-sizing: border-box; margin: 0; padding: 0; }
  html, body { width: 1200px; height: 840px; overflow: hidden; }
  body {
    background: var(--stage);
    font-family: "EB Garamond", "Times New Roman", serif;
    position: relative;
  }
  .card {
    position: absolute;
    width: 560px;
    height: 320px;
    border-radius: 22px;
    overflow: hidden;
    box-shadow: 0 18px 40px rgba(0,0,0,.45);
  }
  /* Back side */
  .card--back {
    left: 40px; top: 80px;
    background: linear-gradient(135deg, var(--teal-deep) 0%, var(--teal) 55%, var(--teal-deep) 100%);
    display: flex; align-items: center; justify-content: center;
  }
  .seal {
    width: 200px; height: 200px;
    border: 1.5px solid var(--paper);
    border-radius: 50%;
    display: flex; align-items: center; justify-content: center;
    text-align: center;
  }
  .seal__name {
    color: var(--paper);
    font-weight: 400;
    font-size: 25px;
    line-height: 1.15;
    letter-spacing: 2px;
    text-transform: uppercase;
  }
  /* Front side */
  .card--front {
    left: 600px; top: 440px;
    background: var(--paper);
  }
  .front__panel {
    position: absolute; left: 0; top: 0;
    width: 250px; height: 320px;
    background: var(--teal-deep);
  }
  .front__floral {
    position: absolute;
    left: 50px; top: 60px;
    width: 150px; height: 190px;
    border-radius: 40%;
    background: radial-gradient(ellipse at center, var(--teal-soft) 0%, var(--teal) 60%, var(--teal-deep) 100%);
  }
  .front__seal {
    position: absolute; right: 30px; top: 22px;
    width: 92px; height: 92px;
    border: 1px solid var(--ink);
    border-radius: 50%;
    display: flex; align-items: center; justify-content: center; text-align: center;
  }
  .front__seal-name {
    color: var(--ink);
    font-weight: 400;
    font-size: 11px;
    line-height: 1.2;
    letter-spacing: 1px;
    text-transform: uppercase;
  }
  .contact {
    position: absolute; right: 30px; top: 128px;
    width: 260px;
    text-align: right;
  }
  .contact__name {
    color: var(--ink);
    font-weight: 700;
    font-size: 24px;
    letter-spacing: 0.5px;
    text-transform: uppercase;
    line-height: 1;
    white-space: nowrap;
  }
  .contact__role { color: var(--ink-muted); font-size: 16px; margin: 4px 0 12px; }
  .contact__list { list-style: none; }
  .contact__item {
    display: flex; justify-content: flex-end; align-items: center; gap: 8px;
    color: var(--ink-muted); font-size: 16px; line-height: 1.45;
    white-space: nowrap;
  }
  .icon { width: 15px; height: 15px; flex: none; }
</style>
</head>
<body>

<section class="card card--back" aria-label="Card back">
  <div class="seal">
    <p class="seal__name">Rosalind<br>Thorpe<br>Gardens</p>
  </div>
</section>

<section class="card card--front" aria-label="Card front">
  <div class="front__panel">
    <div class="front__floral" role="img" aria-label="Line-drawn wildflower sprig with buds and leaves"></div>
  </div>

  <div class="front__seal">
    <p class="front__seal-name">Rosalind<br>Thorpe<br>Gardens</p>
  </div>

  <div class="contact">
    <h1 class="contact__name">Corinne Haldwick</h1>
    <p class="contact__role">Owner</p>
    <ul class="contact__list">
      <li class="contact__item">913-555-0147
        <svg class="icon" viewBox="0 0 16 16" aria-hidden="true"><path fill="var(--ink)" d="M3.5 1.5 6 1l1.3 3.2-1.6 1.2a8 8 0 0 0 4.9 4.9l1.2-1.6L15 10l-.5 2.5C14 14 12.5 15 11 14.8 5.8 14 2 10.2 1.2 5 1 3.5 2 2 3.5 1.5Z"/></svg>
      </li>
      <li class="contact__item">Rosalind Thorpe Gardens
        <svg class="icon" viewBox="0 0 16 16" aria-hidden="true"><circle cx="8" cy="8" r="7" fill="var(--ink)"/></svg>
      </li>
      <li class="contact__item">@RosalindThorpeGardens
        <svg class="icon" viewBox="0 0 16 16" aria-hidden="true"><circle cx="8" cy="8" r="7" fill="var(--ink)"/></svg>
      </li>
      <li class="contact__item">RosalindThorpeGardens.example
        <svg class="icon" viewBox="0 0 16 16" aria-hidden="true"><circle cx="8" cy="8" r="7" fill="none" stroke="var(--ink)" stroke-width="1.5"/><path d="M1 8h14M8 1c-3 3.5-3 10.5 0 14M8 1c3 3.5 3 10.5 0 14" fill="none" stroke="var(--ink)" stroke-width="1.2"/></svg>
      </li>
    </ul>
  </div>
</section>

</body>
</html>
```